Breakfast Cafe - The Sunny Nook

It is for my breakfast and lunch cafe with a hawaiian / beach theme. I am open 7 days a week from 7am to 2pm. We serve traditional American food such as omelettes, pancakes, burgers and sandwiches. I'll upload my old card and my new logo to be used. We have a lot of day to day regulars who eat there during the week, our t-shirts actually say 'Locals Only' on them. Hope this helps. Thanks.

Target Market(s)

anyone who has an appetite!

Industry/Entity Type

American Restaurant

Contact Information for Business Card

4815C Marlow Grove Avenue
Long Beach, California
(555) 731-2294

Requirements
Must have
• Address and phone number easily readable.
Nice to have
• beach or tropical theme

```html
<!DOCTYPE html>
<html lang="en">
<head>
<meta charset="utf-8">
<title>The Sunny Nook – Business Card</title>
<link rel="stylesheet" href="https://fonts.googleapis.com/css2?family=Lato:wght@400;700;900&display=swap">
<style>
  :root {
    --page-bg: #1c1c1c;
    --card-white: #efefef;
    --ink: #222222;
    --accent-orange: #c0691c;
    --accent-sky: #4cc3e6;
    --sea-teal: #3d7f8e;
    --sand-brown: #8a6440;
    --tiki-brown: #7a4a1e;
  }
  * { box-sizing: border-box; margin: 0; padding: 0; }
  html, body {
    width: 1200px; height: 900px; overflow: hidden;
    background: var(--page-bg);
    font-family: "Lato", sans-serif;
  }
  .canvas {
    width: 1200px; height: 900px;
    display: flex; align-items: center; justify-content: center; gap: 40px;
  }
  .card {
    position: relative;
    width: 540px; height: 310px;
    border-radius: 24px;
    overflow: hidden;
  }
  .card-front .artwork {
    position: absolute; inset: 0;
    background: linear-gradient(180deg, var(--sea-teal) 0%, #5a9aa6 45%, var(--tiki-brown) 62%, var(--sand-brown) 100%);
  }
  .menu-line {
    position: absolute; left: 0; right: 0; bottom: 34px;
    text-align: center;
    font-weight: 700; font-size: 24px;
    color: var(--accent-sky);
    -webkit-text-stroke: 0;
    text-shadow: 0 0 3px #fff, 0 0 3px #fff, 0 0 2px #fff;
  }
  .card-back {
    background: var(--card-white);
    padding: 30px 40px;
  }
  .brand-name {
    font-weight: 900; font-size: 46px; line-height: 1;
    color: var(--accent-sky);
  }
  .brand-place {
    margin-top: 6px; margin-left: 110px;
    font-weight: 700; font-size: 13px; letter-spacing: 4px;
    color: var(--accent-orange);
  }
  .tagline {
    margin-top: 14px;
    font-size: 22px; color: var(--accent-orange);
  }
  .contact { margin-top: 10px; color: var(--ink); font-size: 18px; line-height: 1.3; }
  .phone { display: flex; align-items: center; gap: 8px; }
  .phone-icon { width: 20px; height: 20px; }
  .address { margin-top: 8px; margin-left: 28px; }
  .hours {
    margin-top: 12px; margin-left: 28px;
    font-size: 22px; color: var(--accent-orange);
  }
</style>
</head>
<body>
<main class="canvas">
  <section class="card card-front">
    <div class="artwork" role="img" aria-label="Cartoon beach scene illustration: carved tiki figure holding a coffee mug and frying pan with waves behind on sand"></div>
    <p class="menu-line">Omelettes | Pancakes | Burgers | Sandwiches</p>
  </section>

  <section class="card card-back">
    <h1 class="brand-name">The Sunny Nook</h1>
    <p class="brand-place">LONG BEACH, CA</p>
    <p class="tagline">Family owned and operated!</p>
    <div class="contact">
      <p class="phone">
        <svg class="phone-icon" viewBox="0 0 20 20" aria-hidden="true">
          <rect width="20" height="20" rx="3" fill="var(--accent-orange)"/>
          <path d="M6 4.5c.6-.4 1.3-.2 1.6.4l.9 1.8c.3.5.1 1.1-.3 1.4l-.8.6c.6 1.4 1.6 2.5 3 3.2l.6-.8c.4-.4 1-.5 1.4-.2l1.7 1c.6.3.7 1.1.3 1.6l-.9 1c-.6.6-1.5.8-2.3.5C8 13.8 6 11.7 4.9 8.9c-.3-.8-.1-1.7.5-2.3z" fill="#fff"/>
        </svg>
        (555) 731-2294
      </p>
      <p class="address">4815C Marlow Grove Avenue<br>Long Beach, California</p>
    </div>
    <p class="hours">Breakfast &amp; Lunch 7am - 2pm Daily</p>
  </section>
</main>
</body>
</html>
```